Optometrist A5 flyer update 2014

We are an optical / optometrist business needing an existing A5 flyer updated. This flyer has been very successful but needs to be renewed.
We are supplying all the original source files including images.
I have included pdf files with annotations on the alteration we would like made.
We are open to suggestions / alterations to the design of the pamphlet.
We are after a modern design appealing to the various ages of our patient base.

```html
<!DOCTYPE html>
<html lang="en">
<head>
<meta charset="utf-8">
<title>Kirrane Lane Optical – Frequently Asked Questions</title>
<link rel="stylesheet" href="https://fonts.googleapis.com/css2?family=Open+Sans:ital,wght@0,300;0,400;0,600;0,700;1,700&display=swap">
<style>
  :root {
    --green: #1f9a32;
    --navy: #2b3990;
    --navy-deep: #1a2a8c;
    --ink: #1a1a1a;
    --grey-text: #3a3a3a;
    --rule: #7d86c4;
    --white: #ffffff;
  }
  * { margin: 0; padding: 0; box-sizing: border-box; }
  html, body { width: 846px; height: 1200px; overflow: hidden; background: var(--white); }
  body { font-family: "Open Sans", Arial, sans-serif; color: var(--ink); }

  .flyer { position: relative; width: 846px; height: 1200px; overflow: hidden; background: var(--white); }

  .band-green { position: absolute; left: 0; top: 0; width: 846px; height: 44px; background: var(--green); }
  .band-navy { position: absolute; left: 0; top: 44px; width: 846px; height: 52px; background: var(--navy); }

  .hero-photo {
    position: absolute; left: 0; top: 96px; width: 846px; height: 414px;
    background: linear-gradient(100deg, #e9e9ea 0%, #f6f6f6 35%, #dcdcde 60%, #f2f2f3 100%);
  }

  .faq-title {
    position: absolute; left: 399px; top: 484px;
    font-size: 29px; font-weight: 300; line-height: 38px; color: var(--grey-text); letter-spacing: 0.2px;
  }

  .portrait-frame {
    position: absolute; left: 0; top: 528px; width: 366px; height: 462px;
    border: 11px solid var(--navy); border-left: none;
    background: linear-gradient(135deg, #f3e3d8 0%, #e9cdbb 50%, #f6ece4 100%);
  }

  .faq-item { position: absolute; left: 408px; width: 384px; padding-left: 16px; }
  .faq-item--sun { top: 535px; }
  .faq-item--lenses { top: 701px; }
  .faq-item--fund { top: 880px; }
  .faq-arrow { position: absolute; left: 0; top: 4px; width: 9px; height: 13px; }
  .faq-question {
    font-size: 15.5px; font-weight: 700; font-style: italic; color: var(--navy-deep);
    line-height: 20px;
  }
  .faq-question.plain { font-weight: 400; font-style: normal; }
  .faq-answer { font-size: 16px; line-height: 20.5px; color: var(--ink); }

  .faq-rule { position: absolute; left: 420px; width: 366px; height: 1px; background: var(--rule); }
  .faq-rule--one { top: 680px; }
  .faq-rule--two { top: 862px; }

  .web-address {
    position: absolute; left: 148px; top: 1007px;
    font-size: 23px; line-height: 26px; color: var(--navy-deep); letter-spacing: 1.6px;
  }

  .hours-panel {
    position: absolute; left: 0; top: 1039px; width: 442px; height: 161px; background: var(--navy);
    color: var(--white);
  }
  .hours-label {
    position: absolute; left: 12px; top: 150px; transform: rotate(-90deg); transform-origin: left top;
    font-size: 18px; font-weight: 700; line-height: 24px; white-space: nowrap; width: 150px;
  }
  .hours-table { position: absolute; left: 78px; top: 10px; border-collapse: collapse; }
  .hours-table td {
    font-size: 16.5px; font-weight: 700; letter-spacing: 1.2px; line-height: 21.6px; padding: 0;
  }
  .hours-table .day { width: 156px; }

  .brand-name {
    position: absolute; left: 500px; top: 1048px; width: 270px; text-align: center;
    font-size: 34px; font-weight: 400; line-height: 44px; color: var(--navy);
  }
</style>
</head>
<body>
<main class="flyer">
  <div class="band-green"></div>
  <div class="band-navy"></div>

  <div class="hero-photo" role="img" aria-label="Photo of an optometrist in a white coat holding up two pairs of spectacle frames in front of an eye chart"></div>

  <h1 class="faq-title">Frequently Asked Questions</h1>

  <div class="portrait-frame" role="img" aria-label="Photo of a smiling woman wearing red rimless glasses"></div>

  <div class="faq-item faq-item--sun">
    <svg class="faq-arrow" viewBox="0 0 9 13"><polygon points="0,0 9,6.5 0,13" fill="#1f9a32"/></svg>
    <p class="faq-question">Can I have fashion sunglasses made to my prescription?</p>
    <p class="faq-answer">Yes. It does depend on the sunglasses and your prescription.<br>We offer a range of sunglasses that can be fitted with prescription lenses.</p>
  </div>
  <div class="faq-rule faq-rule--one"></div>

  <div class="faq-item faq-item--lenses">
    <svg class="faq-arrow" viewBox="0 0 9 13"><polygon points="0,0 9,6.5 0,13" fill="#1f9a32"/></svg>
    <p class="faq-question">If I want new prescription lenses fitted to my existing pair of glasses, do I have to go without them for a week?</p>
    <p class="faq-answer">No. We can usually fit new lenses to your own frame onsite.<br>You only need to be without your glasses for a few hours.</p>
  </div>
  <div class="faq-rule faq-rule--two"></div>

  <div class="faq-item faq-item--fund">
    <svg class="faq-arrow" viewBox="0 0 9 13"><polygon points="0,0 9,6.5 0,13" fill="#1f9a32"/></svg>
    <p class="faq-question plain">Do I have to purchase my spectacles where my private health fund directs?</p>
    <p class="faq-answer">No. It is your decision where to have your eyes tested and where to purchase your spectacles or contact lenses. We can direct bill your private health fund with the ClaimLink system.</p>
  </div>

  <p class="web-address">www.kirranelaneoptical.com.au</p>

  <section class="hours-panel">
    <h2 class="hours-label">Opening Hours</h2>
    <table class="hours-table">
      <tr><td class="day">Monday</td><td>9.00am - 5.30pm</td></tr>
      <tr><td class="day">Tuesday</td><td>9.00am - 6.30pm</td></tr>
      <tr><td class="day">Wednesday</td><td>9.00am - 5.30pm</td></tr>
      <tr><td class="day">Thursday</td><td>9.00am to 6.30pm</td></tr>
      <tr><td class="day">Friday</td><td>9.00am - 5.30pm</td></tr>
      <tr><td class="day">Saturday</td><td>9.00am - 1.00pm</td></tr>
    </table>
  </section>

  <p class="brand-name">Kirrane Lane<br>Optical</p>
</main>
</body>
</html>
```